Design a refer a friend Flyer (French & English)
Flyer Title:
Main Title: "Refer a Friend & Receive a Free Electric Toothbrush!"
Bold and clear, centered at the top.
Use a clean and modern font.
Color: White text on a vivid green background for maximum contrast and readability.
Visual Focus:
Toothbrush Image: Place a high-quality image of the Dentiva Max 300 Electric Toothbrush in the center of the flyer.
Include a small price tag with “Value of $50” near the toothbrush to highlight the reward.
Simple Message:
Text: "Refer a friend to Centre Dentaire Lac-Ombré. When they book and attend their appointment, you get a free electric toothbrush, and they receive a special gift!"
Straightforward and easy to understand.
Placed below the image of the toothbrush.
Referral Process:
3 Easy Steps:
Refer a Friend
They Book and Come to Their Appointment
Receive Your Free Electric Toothbrush
Use simple, minimal icons to visually represent each step.
Keep the steps aligned horizontally or vertically for clarity.
Call to Action:
Text: "Start Referring Today!"
Place it in a button-like design in the vivid green color with bold, white text to make it stand out.
Contact Information:
Details:
Logo of Centre Dentaire Lac-Ombré.
Address: "42 Rue Valmonde Ouest, Suite 310".
Phone Number and Website: Positioned at the bottom for easy reference.
Color Scheme:
Use a vivid green background for the entire flyer, with white accents for text and icons to maintain a fresh, clean look.
Minimal clutter, focusing on clarity and the key elements: the toothbrush, the call to action, and contact information.
Clinic : www.cdlacombre.example
Attached is the brandbook, logo and inspo I made with AI.
French text will be provided.
Thank you,
Tarin

```html
<!DOCTYPE html>
<html lang="en">
<head>
<meta charset="utf-8">
<title>Refer a Friend Flyer – Centre Dentaire Lac-Ombré</title>
<link href="https://fonts.googleapis.com/css2?family=Poppins:wght@400;500;600;700;800;900&family=Roboto:wght@500;700&display=swap" rel="stylesheet">
<style>
  :root{
    --page-bg:#b3b3b3;
    --forest:#0b2914;
    --green:#3fae55;
    --green-light:#57c26b;
    --accent-green:#4fd36e;
    --link-green:#2e9e45;
    --white:#ffffff;
    --ink:#111111;
    --red:#d4141c;
  }
  *{margin:0;padding:0;box-sizing:border-box}
  html,body{width:1200px;height:1008px;overflow:hidden;background:var(--page-bg)}
  body{font-family:"Poppins",sans-serif;position:relative}

  .flyer{
    position:absolute;left:226px;top:20px;width:798px;height:1033px;
    transform:scale(0.937);transform-origin:top left;
    background:radial-gradient(ellipse at 60% 45%,var(--green-light),var(--green) 70%);
    overflow:hidden;
  }
  .abs{position:absolute}

  .header-band{left:0;top:0;width:798px;height:230px}
  .headline-small{left:66px;top:62px;color:var(--white);font-weight:500;font-size:35px;letter-spacing:9px;line-height:1}
  .headline-green{left:62px;top:98px;color:var(--accent-green);font-weight:800;font-size:60px;line-height:1;letter-spacing:-0.5px}
  .headline-free{left:468px;top:52px;color:var(--white);font-weight:900;font-size:110px;line-height:1;letter-spacing:-1px}

  .product-photo{left:412px;top:196px;width:362px;height:650px;
    background:
      radial-gradient(ellipse 60% 22% at 48% 85%,rgba(250,236,236,.85),rgba(240,190,195,.55) 55%,rgba(240,190,195,0) 100%),
      radial-gradient(ellipse 20% 60% at 78% 42%,rgba(28,34,48,.75),rgba(28,34,48,0) 100%),
      radial-gradient(ellipse 55% 25% at 40% 28%,rgba(30,110,50,.35),rgba(30,110,50,0) 100%);}

  .title-strip{left:62px;top:193px;width:590px;height:80px;background:var(--white);
    clip-path:polygon(0 8%,6% 2%,14% 9%,25% 3%,38% 8%,50% 0,63% 7%,76% 2%,88% 9%,100% 3%,99% 92%,86% 100%,72% 93%,58% 99%,44% 92%,30% 100%,16% 93%,4% 99%,1% 90%)}
  .title-strip-text{left:95px;top:208px;font-weight:800;font-size:40px;color:var(--forest);letter-spacing:-0.5px;line-height:1.2}

  .intro-title{left:62px;top:310px;color:var(--white);font-weight:700;font-size:21.5px;line-height:1.3}
  .intro-body{left:62px;top:382px;padding-left:16px;border-left:4px solid var(--white);
    color:var(--forest);font-size:14.3px;line-height:1.22;width:290px}

  .steps-num{left:56px;top:470px;font-weight:800;font-size:86px;color:var(--ink);line-height:1}
  .steps-kicker{left:113px;top:484px;font-size:22px;letter-spacing:3px;color:var(--white);line-height:1}
  .steps-kicker b{font-weight:800}
  .steps-big{left:112px;top:505px;font-size:43px;color:var(--ink);line-height:1.1}
  .steps-big b{font-weight:800;color:var(--white)}

  .step-tab{left:0;width:118px;height:80px;background:var(--white)}
  .tab1{top:582px;clip-path:polygon(0 0,100% 0,94% 30%,99% 60%,92% 100%,0 100%)}
  .tab2{top:658px;background:#e4e4e4;clip-path:polygon(0 4%,92% 0,98% 40%,93% 70%,97% 100%,0 96%)}
  .tab3{top:724px;background:#d2d2d2;clip-path:polygon(0 0,97% 2%,92% 45%,99% 75%,94% 100%,0 100%)}
  .step-label{left:50px;font-size:11px;font-weight:700;color:var(--ink);transform:rotate(-90deg);transform-origin:left top;letter-spacing:.5px}
  .step-digit{left:78px;font-size:44px;font-weight:800;color:var(--red);line-height:1}
  .step-text{left:137px;color:var(--white);font-weight:700;font-size:16.5px;line-height:1.2}
  .step-rule{left:140px;width:206px;border-top:2px dotted var(--forest)}

  .value-badge{left:427px;top:491px;width:180px;height:180px}

  .footer-white{left:0;top:855px;width:798px;height:178px}
  .cta-band{left:0;top:852px;width:392px;height:58px;background:var(--forest);
    clip-path:polygon(0 4%,30% 0,60% 6%,100% 0,98% 100%,60% 94%,30% 100%,0 95%)}
  .cta-text{left:62px;top:866px;color:var(--white);font-weight:800;font-size:22px;line-height:1.2}
  .cta-text span{color:var(--accent-green)}

  .clinic-name{left:60px;top:935px;font-family:"Roboto",sans-serif;font-weight:700;font-size:35px;color:var(--ink);line-height:1}
  .clinic-sub{left:61px;top:975px;font-family:"Roboto",sans-serif;font-weight:700;font-size:15px;color:var(--ink)}
  .divider{left:438px;top:940px;width:2px;height:48px;background:var(--link-green)}

  .address{left:455px;top:893px;font-weight:700;font-size:16.5px;color:var(--ink);display:flex;align-items:center;gap:5px;white-space:nowrap;line-height:1.2}
  .phone-row{left:465px;top:932px;display:flex;align-items:center;gap:6px;color:var(--ink);white-space:nowrap}
  .phone-row .call{font-weight:600;font-size:15px}
  .phone-row .number{font-weight:700;font-size:23px}
  .web{left:466px;top:960px;font-size:19px;letter-spacing:1.6px;color:var(--ink);white-space:nowrap}
  .web b{color:var(--link-green);font-weight:600}
</style>
</head>
<body>
<section class="flyer">
  <svg class="abs header-band" viewBox="0 0 798 230" preserveAspectRatio="none" aria-hidden="true">
    <polygon fill="var(--forest)" points="0,0 798,0 798,205 760,200 720,212 680,198 640,210 600,214 560,210 520,220 470,212 420,222 360,214 300,224 240,214 180,222 120,214 60,226 20,216 0,222"/>
  </svg>
  <div class="abs headline-small">REFER A FRIEND</div>
  <div class="abs headline-green">&amp; RECEIVE A</div>
  <div class="abs headline-free">FREE</div>

  <div class="abs product-photo" role="img" aria-label="Photo of the Dentiva Max 300 electric toothbrush standing upright beside a dental jaw model with a probe, over a faint world map"></div>

  <div class="abs title-strip"></div>
  <div class="abs title-strip-text">ELECTRIC TOOTHBRUSH!</div>

  <div class="abs intro-title">Refer a friend to Centre<br>Dentaire Lac-Ombré.</div>
  <p class="abs intro-body">When they book and attend their appointment, you get a free electric toothbrush, and they receive a special gift!</p>

  <div class="abs steps-num">3</div>
  <div class="abs steps-kicker"><b>REFERRAL</b> PROCESS</div>
  <div class="abs steps-big"><b>EASY</b> STEPS</div>

  <div class="abs step-tab tab1"></div>
  <div class="abs step-tab tab2"></div>
  <div class="abs step-tab tab3"></div>
  <div class="abs step-label" style="top:636px">STEP</div>
  <div class="abs step-label" style="top:712px">STEP</div>
  <div class="abs step-label" style="top:781px">STEP</div>
  <div class="abs step-digit" style="top:597px">1</div>
  <div class="abs step-digit" style="top:673px">2</div>
  <div class="abs step-digit" style="top:741px">3</div>
  <div class="abs step-text" style="top:606px">Refer a Friend</div>
  <div class="abs step-rule" style="top:652px"></div>
  <div class="abs step-text" style="top:672px">They Book and Come to<br>Their Appointment</div>
  <div class="abs step-rule" style="top:733px"></div>
  <div class="abs step-text" style="top:756px">Receive Your Free<br>Electric Toothbrush</div>

  <svg class="abs value-badge" viewBox="0 0 180 180" aria-label="Value of $50">
    <polygon fill="var(--red)" points="90,0 101,13 115,4 122,19 138,15 140,31 156,32 153,48 168,54 160,68 173,78 162,90 173,102 160,112 168,126 153,132 156,148 140,149 138,165 122,161 115,176 101,167 90,180 79,167 65,176 58,161 42,165 40,149 24,148 27,132 12,126 20,112 7,102 18,90 7,78 20,68 12,54 27,48 24,32 40,31 42,15 58,19 65,4 79,13"/>
    <text x="90" y="58" text-anchor="middle" font-family="Poppins, sans-serif" font-weight="800" font-size="23" fill="var(--ink)">VALUE</text>
    <text x="90" y="80" text-anchor="middle" font-family="Poppins, sans-serif" font-weight="500" font-size="20" fill="var(--white)">OF</text>
    <text x="94" y="132" text-anchor="middle" font-family="Poppins, sans-serif" font-weight="800" font-size="58" fill="var(--white)"><tspan font-size="30" dy="-20">$</tspan><tspan dy="20">50</tspan></text>
  </svg>

  <svg class="abs footer-white" viewBox="0 0 798 178" preserveAspectRatio="none" aria-hidden="true">
    <polygon fill="var(--white)" points="0,40 390,40 420,20 470,14 520,20 570,12 620,18 670,10 720,16 760,8 798,12 798,178 0,178"/>
  </svg>
  <div class="abs cta-band"></div>
  <div class="abs cta-text">START REFERRING <span>TODAY!</span></div>

  <div class="abs clinic-name">Clinique Dentaire</div>
  <div class="abs clinic-sub">Lac-Ombré</div>
  <div class="abs divider"></div>

  <div class="abs address">
    <svg width="13" height="17" viewBox="0 0 14 18" aria-hidden="true"><path d="M7 0C3.1 0 0 3.1 0 7c0 5 7 11 7 11s7-6 7-11c0-3.9-3.1-7-7-7zm0 9.5A2.5 2.5 0 1 1 7 4.5a2.5 2.5 0 0 1 0 5z" fill="var(--red)"/></svg>
    42 Rue Valmonde Ouest, Suite 310
  </div>
  <div class="abs phone-row">
    <span class="call">Call us now!</span>
    <svg width="18" height="18" viewBox="0 0 18 18" aria-hidden="true"><circle cx="9" cy="9" r="8" fill="none" stroke="var(--link-green)" stroke-width="2"/><path d="M6 5.5l1.5-.5 1 2-1 1c.5 1 1.3 1.8 2.3 2.3l1-1 2 1-.5 1.5c-3 0-6.3-3.3-6.3-6.3z" fill="var(--link-green)"/></svg>
    <span class="number">514 555 0182</span>
  </div>
  <div class="abs web">www.<b>cdlacombre</b>.example</div>
</section>
</body>
</html>
```